Natural Light/Organic/Documentary Photography Business

I like a simple, approachable, feminine, earthy/organic feel. Earth/neutral tones, nothing too loud or obnoxious. I like the watercolor look. I don't want anything too trendy or something I'll get tired of after a couple months. As far as colors, I am much more a fan of cream/taupe/blue/green...not a fan of pink or purple at all.

Target Market(s)

Weddings & Families

Industry/Entity Type

Wedding Photography

Contact Information for Business Card

website, email, phone number

Font styles to use
Other font styles liked:
• Horizontes, Gotham

Colors

Designer to choose colors to be used in the design.

Requirements
Must have
• Website: www.mirelhatchway.com
• Phone: 418.629.5073
• Email: mirel@mirelhatchway.com
Nice to have
• I like the watercolor look but its not necessary. I like simple/earthy tones. Nothing too loud or distracting. Simple & feminine without being too girly. I like an approachable/soft feel.
• Instagram: www.instagram.com/mirelhatchwayphotography/
Should not have
• NO loud colors or design or pattern. I do not want a photo of a camera or lens or anything cheesy like that.

```html
<!DOCTYPE html>
<html lang="en">
<head>
<meta charset="utf-8">
<title>Mirel Hatchway Photography – Business Card</title>
<link href="https://fonts.googleapis.com/css2?family=Open+Sans:wght@400&display=swap" rel="stylesheet">
<style>
  :root {
    --backdrop: #6e6e6e;
    --card-white: #ffffff;
    --card-mist: #efefef;
    --ink: #2f2f2f;
    --taupe: #8a7a70;
    --rule: #5a5a5a;
    --peach: #f1bb9c;
    --cream: #f6efe6;
    --stone: #d9d5cc;
    --forest: #1f3b38;
    --accent-blue: #2d6aa6;
  }
  * { margin: 0; padding: 0; box-sizing: border-box; }
  html, body { width: 1200px; height: 1200px; overflow: hidden; }
  body {
    background: var(--backdrop);
    font-family: "Open Sans", Arial, sans-serif;
    position: relative;
  }
  .card {
    position: absolute;
    top: 310px;
    height: 594px;
    overflow: hidden;
    box-shadow: 2px 3px 6px rgba(0,0,0,0.35);
  }
  .card--front { left: 234px; width: 364px; background: var(--card-white); }
  .card--back { left: 627px; width: 369px; background: var(--card-mist); }

  .wash {
    position: absolute;
    left: 0;
    width: 100%;
    background: linear-gradient(100deg, var(--peach) 0%, var(--cream) 40%, var(--stone) 72%, var(--forest) 100%);
  }
  .wash--front { top: 0; height: 466px; }
  .wash--back { bottom: 0; height: 112px; }

  .brand {
    position: absolute;
    left: 0;
    width: 100%;
    text-align: center;
    color: var(--taupe);
    font-weight: 400;
  }
  .brand__name { font-size: 34px; letter-spacing: 1px; line-height: 1; }
  .brand__tag { font-size: 8px; letter-spacing: 5px; margin-top: 8px; padding-left: 5px; }
  .card--front .brand { top: 497px; }
  .card--back .brand { top: 146px; }

  .divider {
    position: absolute;
    left: 66px;
    width: 238px;
    height: 24px;
  }
  .divider--contact { top: 227px; }
  .divider--social { top: 346px; }

  .contact {
    position: absolute;
    left: 0;
    width: 100%;
    text-align: center;
    color: var(--ink);
    font-size: 17px;
    line-height: 21.5px;
  }
  .contact--main { top: 256px; }
  .contact--social { top: 376px; color: #444; }
</style>
</head>
<body>
  <section class="card card--front" aria-label="Card front">
    <div class="wash wash--front" role="img" aria-label="Watercolour artwork in peach, cream, stone grey and deep forest green"></div>
    <div class="brand">
      <div class="brand__name">Mirel Hatchway</div>
      <div class="brand__tag">PHOTOGRAPHY</div>
    </div>
  </section>

  <section class="card card--back" aria-label="Card back">
    <div class="brand">
      <div class="brand__name">Mirel Hatchway</div>
      <div class="brand__tag">PHOTOGRAPHY</div>
    </div>

    <svg class="divider divider--contact" viewBox="0 0 238 24" aria-hidden="true">
      <line x1="0" y1="12" x2="84" y2="12" stroke="var(--rule)" stroke-width="1.2"/>
      <line x1="154" y1="12" x2="238" y2="12" stroke="var(--rule)" stroke-width="1.2"/>
      <g fill="none" stroke="var(--taupe)" stroke-width="1.4">
        <circle cx="96" cy="12" r="8"/>
        <circle cx="119" cy="12" r="8"/>
        <circle cx="142" cy="12" r="8"/>
      </g>
      <path d="M92.5 8.5 q1 -1 2 0 l0.8 1.6 q-0.6 0.8 -0.2 1.6 q0.9 1.6 2.2 2.2 q0.8 0.4 1.6 -0.2 l1.6 0.8 q1 1 0 2 q-2 1.2 -5 -1.4 q-3.2 -3 -3 -6.6z" fill="var(--taupe)"/>
      <rect x="114.5" y="8.5" width="9" height="7" rx="1" fill="var(--taupe)"/>
      <path d="M114.8 9 l4.2 3.5 l4.2 -3.5" stroke="var(--card-mist)" stroke-width="1" fill="none"/>
      <circle cx="142" cy="12" r="4.6" fill="var(--taupe)"/>
      <path d="M137.4 12 h9.2 M142 7.4 q-2.4 4.6 0 9.2 M142 7.4 q2.4 4.6 0 9.2" stroke="var(--card-mist)" stroke-width="0.8" fill="none"/>
    </svg>

    <div class="contact contact--main">
      <div>418.629.5073</div>
      <div>mirel@mirelhatchway.com</div>
      <div>www.mirelhatchway.com</div>
    </div>

    <svg class="divider divider--social" viewBox="0 0 238 24" aria-hidden="true">
      <line x1="0" y1="12" x2="98" y2="12" stroke="var(--rule)" stroke-width="1.2"/>
      <line x1="140" y1="12" x2="238" y2="12" stroke="var(--rule)" stroke-width="1.2"/>
      <circle cx="119" cy="12" r="10" fill="var(--accent-blue)"/>
    </svg>

    <div class="contact contact--social">mirelhatchwayphotography</div>

    <div class="wash wash--back" role="img" aria-label="Watercolour band in peach, cream, stone grey and deep forest green"></div>
  </section>
</body>
</html>
```